Calden L - Premium Business Cards

Background of Calden L
Calden Leafworks is a cigar mobile lounge where guests become family. A place of luxury, relaxation, and ambiance is the global popularity demand. Calden Leafworks strives to provide first-class service of quality and products. Our goal is to ensure that every guest is treated and serviced as a VIP.

Calden Leafworks was founded by Dennis Markow Jr in January 2020. After 15 years of cigar reviews and research Dennis decided it was time to launch his own cigar brand and boutique cigar company. With a wealth of knowledge and years of experience Calden Leafworks was born. With opulence for all cultures, Calden Leafworks offers hand rolled cigars with premium blend tobacco from sweet to bold imported from Costa Rica, Dominican Republic, and Nicaragua. Thank you for your business!

Objective:
Create a business card template to be used for all employees. Design should communicate premium and classy. And should use earth tone colors.

Design should include:
1. Client wants to incorporate the cigar leaf
2. Logo
3. Tagline: Savor every leaf
3. Content info:
Kevin Oldacre
Owner
555-017-4863
koldacre@caldenleaf.com
caldenleafworks.com

```html
<!DOCTYPE html>
<html lang="en">
<head>
<meta charset="utf-8">
<title>Calden Leafworks – Business Cards</title>
<link rel="stylesheet" href="https://fonts.googleapis.com/css2?family=Montserrat:wght@700&family=Open+Sans:wght@400;600;700&display=swap">
<style>
  :root {
    --backdrop: #3a3a3a;
    --card-white: #ffffff;
    --card-black: #141414;
    --ink: #1b1b1b;
    --muted: #6f6f6f;
    --teal: #5f8c98;
    --edge: #7fa6b0;
    --logo-dark: #8a8a8a;
    --rule-dark: #555555;
  }
  * { box-sizing: border-box; margin: 0; padding: 0; }
  html, body { width: 1200px; height: 801px; overflow: hidden; }
  body {
    background: radial-gradient(ellipse at 40% 35%, #4a4a4a 0%, var(--backdrop) 70%);
    position: relative;
    font-family: "Open Sans", sans-serif;
  }
  .card {
    position: absolute;
    width: 560px;
    height: 320px;
    border-bottom: 3px solid var(--edge);
  }
  .card-front { left: 70px; top: 70px; background: var(--card-white); }
  .card-back { left: 570px; top: 410px; background: var(--card-black); }

  .brand {
    position: absolute;
    display: flex;
    align-items: center;
    gap: 10px;
    font-family: "Montserrat", sans-serif;
    font-weight: 700;
    text-transform: uppercase;
    letter-spacing: 0.5px;
    white-space: nowrap;
  }
  .brand-dot { width: 10px; height: 10px; border-radius: 50%; flex: none; }
  .card-front .brand { left: 36px; top: 62px; font-size: 20px; color: var(--ink); }
  .card-front .brand-dot { background: var(--ink); }
  .brand-rule { position: absolute; }
  .card-front .brand-rule { left: 36px; top: 100px; }

  .person { position: absolute; right: 34px; top: 40px; text-align: right; }
  .person-name {
    font-weight: 700; font-size: 21px; letter-spacing: 0.5px;
    color: var(--teal); text-transform: uppercase; white-space: nowrap;
  }
  .person-role { font-size: 13px; color: var(--muted); margin-top: -2px; }

  .divider {
    position: absolute; left: 88px; right: 28px; top: 170px;
    height: 1px; background: var(--teal);
  }

  .contacts { position: absolute; left: 112px; top: 186px; list-style: none; }
  .contacts li {
    display: flex; align-items: center; gap: 8px;
    font-size: 15px; color: var(--ink); line-height: 24px; white-space: nowrap;
  }
  .contacts svg { width: 11px; height: 11px; flex: none; }

  .tagline {
    position: absolute; right: 34px; top: 228px;
    font-size: 13px; font-weight: 600; color: var(--ink);
    text-transform: uppercase; letter-spacing: 0.3px; white-space: nowrap;
  }

  .card-back .brand {
    left: 0; right: 0; top: 128px; justify-content: center;
    font-size: 32px; color: var(--logo-dark);
  }
  .card-back .brand-dot { background: var(--logo-dark); }
  .card-back .brand-rule { left: 90px; top: 188px; }
</style>
</head>
<body>

<section class="card card-front">
  <div class="brand"><span class="brand-dot"></span>Calden Leafworks</div>
  <svg class="brand-rule" width="250" height="8" viewBox="0 0 250 8" aria-hidden="true">
    <circle cx="3" cy="4" r="2" fill="#1b1b1b"/>
    <line x1="5" y1="4" x2="245" y2="4" stroke="#1b1b1b" stroke-width="1"/>
    <circle cx="247" cy="4" r="2" fill="#1b1b1b"/>
  </svg>

  <div class="person">
    <p class="person-name">Kevin Oldacre</p>
    <p class="person-role">Owner</p>
  </div>

  <div class="divider"></div>

  <ul class="contacts">
    <li>
      <svg viewBox="0 0 12 12" aria-hidden="true"><circle cx="6" cy="6" r="6" fill="#5f8c98"/><path d="M4 3.2l1 1.4-.6.7a4 4 0 0 0 2.3 2.3l.7-.6 1.4 1-.6 1c-2.6-.2-4.7-2.3-4.9-4.9z" fill="#fff"/></svg>
      555-017-4863
    </li>
    <li>
      <svg viewBox="0 0 12 12" aria-hidden="true"><rect x="1" y="2.5" width="10" height="7" rx="1" fill="#5f8c98"/><path d="M1.5 3l4.5 3.5L10.5 3" fill="none" stroke="#fff" stroke-width="0.9"/></svg>
      koldacre@caldenleaf.com
    </li>
    <li>
      <svg viewBox="0 0 12 12" aria-hidden="true"><circle cx="6" cy="6" r="5.5" fill="#5f8c98"/><ellipse cx="6" cy="6" rx="2.2" ry="5.5" fill="none" stroke="#fff" stroke-width="0.8"/><line x1="0.5" y1="6" x2="11.5" y2="6" stroke="#fff" stroke-width="0.8"/></svg>
      caldenleafworks.com
    </li>
  </ul>

  <p class="tagline">Savor every leaf</p>
</section>

<section class="card card-back">
  <div class="brand"><span class="brand-dot"></span>Calden Leafworks</div>
  <svg class="brand-rule" width="380" height="8" viewBox="0 0 380 8" aria-hidden="true">
    <circle cx="3" cy="4" r="2" fill="#555"/>
    <line x1="5" y1="4" x2="375" y2="4" stroke="#555" stroke-width="1"/>
    <circle cx="377" cy="4" r="2" fill="#555"/>
  </svg>
</section>

</body>
</html>
```